Personal training and nutrition business needs business card design

We need a business card that outlays our services and invites potential customers to join our team and take the first step to a healthier and more enjoyable life. We cater for any level of fitness and specialize in weight loss and conditioning, strength training, muscle gain and strength endurance. Whether you are just starting off or need some help getting to the next level of your journey we are here to get the job done.
We specialize in one on one or one on two personal training sessions and each program will be custom made to suit individual fitness goals of our clients

```html
<!DOCTYPE html>
<html lang="en">
<head>
<meta charset="utf-8">
<title>Stride &amp; Drive — Business Card</title>
<link rel="stylesheet" href="https://fonts.googleapis.com/css2?family=Bebas+Neue&family=Exo+2:ital,wght@1,800&family=Roboto:wght@400;700&display=swap">
<style>
  :root {
    --backdrop: #2b2b2d;
    --card: #1c1c1e;
    --ink: #ececec;
    --ink-soft: #d9d9d9;
    --emboss: #4a4a4d;
    --violet: #a35bc4;
    --violet-deep: #7c46b3;
  }
  * { margin: 0; padding: 0; box-sizing: border-box; }
  html, body { width: 1200px; height: 1138px; overflow: hidden; background: var(--backdrop); }
  body { position: relative; font-family: "Roboto", sans-serif; color: var(--ink); }

  .card {
    position: absolute;
    background: var(--card);
    border-radius: 14px;
    box-shadow: 0 8px 18px rgba(0,0,0,.45);
  }
  .card--front { left: 274px; top: 186px; width: 622px; height: 374px; }
  .card--back  { left: 276px; top: 608px; width: 618px; height: 374px; }

  /* Front */
  .front-brand {
    position: absolute; left: 0; right: 0; top: 150px;
    display: flex; justify-content: center; align-items: center; gap: 14px;
  }
  .front-brand__square { width: 30px; height: 30px; background: var(--emboss); }
  .front-brand__name {
    font-family: "Roboto", sans-serif; font-weight: 700; font-size: 44px;
    letter-spacing: 2px; color: var(--emboss);
  }
  .front-tagline {
    position: absolute; left: 0; right: 0; top: 330px; text-align: center;
    font-family: "Bebas Neue", sans-serif; font-size: 17px; letter-spacing: 1.6px;
    color: var(--violet);
  }

  /* Back */
  .back-brand { position: absolute; left: 40px; top: 52px; display: flex; align-items: center; gap: 14px; }
  .back-brand__square { width: 62px; height: 62px; background: linear-gradient(135deg, var(--violet), var(--violet-deep)); }
  .back-brand__name {
    font-family: "Roboto", sans-serif; font-weight: 700; font-size: 30px; line-height: 30px;
    color: var(--ink);
  }
  .back-brand__tagline {
    font-family: "Bebas Neue", sans-serif; font-size: 10.5px; letter-spacing: .8px;
    color: var(--violet); margin-top: 4px;
  }

  .person { position: absolute; left: 44px; top: 206px; }
  .person__name {
    font-family: "Exo 2", sans-serif; font-style: italic; font-weight: 800; font-size: 27px;
    letter-spacing: 1px; color: var(--violet); line-height: 30px;
  }
  .person__role { font-size: 16px; color: var(--ink-soft); margin-top: 2px; }

  .divider { position: absolute; left: 0; top: 0; }

  .address { position: absolute; left: 44px; top: 294px; font-size: 16px; line-height: 24px; color: var(--ink-soft); }

  .contacts { position: absolute; right: 30px; top: 268px; list-style: none; }
  .contacts li {
    display: flex; justify-content: flex-end; align-items: center; gap: 12px;
    font-size: 16px; line-height: 24px; color: var(--ink-soft);
  }
  .contacts svg { width: 14px; height: 14px; fill: var(--violet); }
</style>
</head>
<body>

<section class="card card--front">
  <div class="front-brand">
    <span class="front-brand__square"></span>
    <span class="front-brand__name">STRIDE &amp; DRIVE</span>
  </div>
  <p class="front-tagline">Personal Training.&nbsp; Nutrition. Motivation</p>
</section>

<section class="card card--back">
  <div class="back-brand">
    <span class="back-brand__square"></span>
    <div>
      <div class="back-brand__name">STRIDE<br>&amp; DRIVE</div>
      <div class="back-brand__tagline">Personal Training.&nbsp; Nutrition. Motivation</div>
    </div>
  </div>

  <div class="person">
    <div class="person__name">MARCUS REED</div>
    <div class="person__role">Personal Trainer</div>
  </div>

  <svg class="divider" width="618" height="374" viewBox="0 0 618 374" aria-hidden="true">
    <path d="M44 274 H318 C342 274 342 242 372 242 H578" fill="none" stroke="var(--violet)" stroke-width="1.6"/>
  </svg>

  <div class="address">1820 Maple Ridge Lane<br>Fairview Texas 75069</div>

  <ul class="contacts">
    <li>+1 (555) 214-7730
      <svg viewBox="0 0 16 16"><path d="M2 6c0-2 3-3 6-3s6 1 6 3v1h-3V5.5H5V7H2zM4 8h8l2 5H2z"/></svg>
    </li>
    <li>marcus@strideanddrive.com
      <svg viewBox="0 0 16 16"><path d="M1 3h14v10H1zM2.5 4.5 8 9l5.5-4.5" fill="var(--violet)" stroke="var(--card)" stroke-width="1"/></svg>
    </li>
    <li>www.strideanddrive.com
      <svg viewBox="0 0 16 16"><circle cx="8" cy="8" r="7"/><path d="M1 8h14M8 1c-3 3-3 11 0 14M8 1c3 3 3 11 0 14" fill="none" stroke="var(--card)" stroke-width="1"/></svg>
    </li>
  </ul>
</section>

</body>
</html>
```